New homepage and Product page - Lumen Vq

Reason: I have narrowed it done to 3 designers and just need to get the designs revised

Industry/Entity Type

Product

```html
<!DOCTYPE html>
<html lang="en">
<head>
<meta charset="utf-8">
<title>Lumen Vq – Garcinia Cambogia</title>
<link href="https://fonts.googleapis.com/css2?family=Montserrat:wght@300;400;500&family=Open+Sans:wght@400;600;700&family=Caveat:wght@500&display=swap" rel="stylesheet">
<style>
:root{
  --green-top:#5aab12;
  --green-hero:#5fae16;
  --green-hero-dark:#3f8a0c;
  --green-deep:#3e7f10;
  --green-text:#4d8a1f;
  --green-light:#b6ec5a;
  --green-link:#5a9d1c;
  --orange:#ef7c1b;
  --ink:#555;
  --ink-soft:#777;
  --panel:#eeeeec;
  --footer:#ebe8e3;
  --white:#fff;
}
*{margin:0;padding:0;box-sizing:border-box}
html,body{width:1200px;height:1031px;overflow:hidden;background:var(--white)}
body{position:relative;font-family:"Open Sans",Arial,sans-serif;color:var(--ink)}
.abs{position:absolute}

.top-rule{left:0;top:0;width:1200px;height:3px;background:var(--green-top)}
.header{left:0;top:3px;width:1200px;height:66px;background:linear-gradient(#fdfdfd,#f1f1f1)}
.nav{top:30px;font-size:12px;font-weight:600;color:#555}
.brand{left:0;width:1200px;top:22px;text-align:center;font-family:"Montserrat",sans-serif;font-weight:500;font-size:26px;letter-spacing:1px;color:var(--green-deep);z-index:3}
.phone{left:827px;top:24px;font-family:"Montserrat",sans-serif;font-weight:300;font-size:20px;color:#555;white-space:nowrap}

.hero{left:0;top:69px;width:1200px;height:385px;background:radial-gradient(ellipse at 62% 45%,#7cc52a 0%,var(--green-hero) 40%,var(--green-hero-dark) 100%);overflow:hidden}
.hero-tab{left:0;top:69px;width:1200px;height:30px}
.hero-tab-bottom{left:0;top:438px;width:1200px;height:20px}
.tagline{left:0;width:1200px;top:104px;text-align:center;font-family:"Montserrat",sans-serif;font-size:13px;font-weight:500;color:var(--green-light);letter-spacing:.3px}
.hero-title{left:230px;top:168px;font-family:"Montserrat",sans-serif;font-weight:300;font-size:33px;color:var(--white);white-space:nowrap}
.hero-copy{left:230px;top:226px;width:350px;font-size:12.5px;line-height:18px;font-weight:600;color:var(--white)}
.btn{left:231px;top:348px;width:135px;height:39px;border:2px solid var(--white);border-radius:4px;background:var(--orange);color:var(--white);font-family:"Montserrat",sans-serif;font-size:14px;line-height:35px;text-align:center;white-space:nowrap}
.btn span{color:#ffd3a8;margin-left:6px}
.slogan{left:380px;top:347px;font-family:"Caveat",cursive;font-size:27px;color:var(--green-light);transform:rotate(-3deg);white-space:nowrap}
.product-art{left:655px;top:134px;width:335px;height:300px;border-radius:6px;background:linear-gradient(90deg,rgba(240,225,140,.55) 0%,rgba(250,240,180,.6) 22%,rgba(255,255,255,.9) 24%,#f4f1ec 70%,rgba(255,255,255,.85) 100%)}
.arrow{top:238px;width:38px;height:38px;background:#7dc42f;color:#2f5f0a;font-size:16px;line-height:38px;text-align:center;font-weight:700}
.arrow.left{left:0;border-radius:0 3px 3px 0}
.arrow.right{left:1162px;border-radius:3px 0 0 3px}
.dots{left:579px;top:449px;display:flex;gap:5px;z-index:3}
.dots i{display:block;width:11px;height:4px;border-radius:2px;background:#ddd}
.dots i.on{background:var(--green-top)}

.section-title{left:0;width:1200px;top:490px;text-align:center;font-family:"Montserrat",sans-serif;font-weight:300;font-size:30px;color:var(--green-text)}
.section-lede{left:0;width:1200px;top:531px;text-align:center;font-size:16.5px;line-height:24px;color:#666}

.features{left:231px;top:616px;width:736px;height:207px;border:1px solid #ddd;background:linear-gradient(90deg,#fff 0%,#f6f6f5 55%,var(--panel) 100%)}
.features-bar{left:231px;top:616px;width:430px;height:31px;background:var(--green-deep);color:var(--white);font-family:"Montserrat",sans-serif;font-size:15.5px;line-height:31px;padding-left:18px}
.feature{left:248px;width:370px}
.feature h3{font-family:"Montserrat",sans-serif;font-weight:400;font-size:13.5px;color:#444;padding-left:24px;position:relative;white-space:nowrap}
.feature h3 svg{position:absolute;left:0;top:-1px}
.feature p{font-size:11.5px;line-height:17px;color:var(--ink-soft);padding-left:24px;margin-top:3px;white-space:nowrap}
.person-photo{left:622px;top:596px;width:193px;height:227px;border-radius:90px 90px 0 0;background:linear-gradient(#f3e2cf,#f7d4c6 70%,#f5c9bd)}
.guarantee-seal{left:766px;top:640px;width:78px;height:78px;border-radius:50%;background:radial-gradient(#f8c53a,#e0a010);border:3px solid #f3d26a}
.guarantee-head{left:838px;top:646px;width:112px;text-align:right;font-size:12px;line-height:17px;font-weight:700;color:#555;white-space:nowrap}
.guarantee-copy{left:800px;top:731px;width:150px;text-align:right;font-size:12px;line-height:17px;color:var(--ink-soft);white-space:nowrap}

.badge{border-radius:50%;background:#666}
.shield{width:51px;height:52px}
.note{font-size:10.5px;line-height:16px;color:var(--ink-soft);white-space:nowrap}
.note b{color:#555}
.note a{color:var(--green-link);font-weight:700;text-decoration:none}

.footer{left:0;top:931px;width:1200px;height:100px;background:var(--footer);border-top:1px solid #cfcbc4}
.footer-small{font-size:9.5px;color:#777}
.footer-links{left:727px;top:959px;font-size:9.5px;color:var(--green-link);font-weight:600}
.footer-links span{color:#999;margin:0 5px}
.social{top:953px;width:23px;height:23px;border-radius:3px;background:#a5a19b}
</style>
</head>
<body>
<div class="abs top-rule"></div>
<header class="abs header"></header>
<nav>
  <div class="abs nav" style="left:230px">Home</div>
  <div class="abs nav" style="left:303px">Products</div>
  <div class="abs nav" style="left:395px">Contact Us</div>
</nav>
<div class="abs phone">1 800 555 0142</div>

<section class="abs hero" aria-label="Featured product"></section>
<svg class="abs hero-tab" viewBox="0 0 1200 30" preserveAspectRatio="none" aria-hidden="true">
  <path d="M455 0 C490 0 490 24 540 24 L670 24 C720 24 720 0 755 0 Z" fill="#f4f4f4"/>
</svg>
<div class="abs brand">Lumen Vq</div>
<div class="abs tagline">A BRAND YOU CAN TRUST</div>
<div class="abs product-art" role="img" aria-label="Garcinia fruit halves beside the product box"></div>
<h1 class="abs hero-title">GARCINIA CAMBOGIA</h1>
<p class="abs hero-copy">Lumen Vq Garcinia Cambogia is made with 100% pure natural ingredients. Unlike other products, Lumen Vq Garcinia Cambogia is made with premium garcinia cambogia that supplies 60% HCA, which is the active weight-loss component of garcinia cambogia.</p>
<div class="abs btn">LEARN MORE<span>❯</span></div>
<div class="abs slogan">Start Losing Weight Today!</div>
<div class="abs arrow left">❮</div>
<div class="abs arrow right">❯</div>
<svg class="abs hero-tab-bottom" viewBox="0 0 1200 20" preserveAspectRatio="none" aria-hidden="true">
  <path d="M525 20 C555 20 555 4 585 4 L630 4 C660 4 660 20 690 20 Z" fill="#fff"/>
</svg>
<div class="abs dots"><i class="on"></i><i></i><i></i></div>

<h2 class="abs section-title">THE BEST OF NATURE &amp; SCIENCE</h2>
<p class="abs section-lede">New Lumen Vq is line of natural, high-quality, weight-loss supplements that are<br>scientifically formulated for better efficiency!</p>

<section class="abs features" aria-label="Product promises"></section>
<div class="abs features-bar">ALL OUR PRODUCTS ARE</div>
<div class="abs feature" style="top:664px">
  <h3><svg width="20" height="20" viewBox="0 0 20 20"><path d="M2 18 C2 8 8 2 19 2 C19 12 12 18 2 18Z" fill="#6cb52a"/></svg>100% PURE NATURAL INGREDIENTS</h3>
  <p>Lumen Vq products are made with 100% pure natural<br>ingredients. Unlike other products, Lumen Vq products are<br>made with premium natural ingredients for effective results.</p>
</div>
<div class="abs feature" style="top:749px">
  <h3><svg width="20" height="20" viewBox="0 0 20 20"><path d="M2 18 C2 8 8 2 19 2 C19 12 12 18 2 18Z" fill="#6cb52a"/></svg>SCIENTIFICALLY FORMULATED</h3>
  <p>Lumen Vq products are scientifically formulated to deliver<br>the exact clinically tested doses that are needed to see results!</p>
</div>
<div class="abs person-photo" role="img" aria-label="Photo of a smiling customer"></div>
<div class="abs guarantee-seal" role="img" aria-label="Money back guarantee seal"></div>
<div class="abs guarantee-head">Lumen Vq<br>is guaranteed to<br>work or your<br>money back</div>
<div class="abs guarantee-copy">Simply return it to the<br>place of purchase within<br>30 days for a refund<br>with original receipt</div>

<div class="abs badge" style="left:230px;top:851px;width:54px;height:54px" role="img" aria-label="Clinically tested seal"></div>
<p class="abs note" style="left:297px;top:857px">Lorem ipsum dolor sit amet, consectetur adipisicing elit, sed<br>do eiusmod incididunt ut labore et dolore magna aliqua<br>enim ad minim laboris nisi ut aliquip ext ... <a>Find out more</a></p>
<svg class="abs shield" style="left:616px;top:855px" viewBox="0 0 51 52" role="img" aria-label="Made in the USA seal"><path d="M3 4 H48 V28 C48 40 36 47 25.5 52 C15 47 3 40 3 28 Z" fill="#888"/></svg>
<p class="abs note" style="left:679px;top:852px"><b>Made in the USA</b><br>Lumen Vq is manufactured in a GMP-compliant<br>manufacturing facility to ensure 100% quality.</p>

<footer class="abs footer"></footer>
<div class="abs footer-small" style="left:230px;top:954px">© Copyright 2014 Lumen Vq</div>
<div class="abs footer-links">Home<span>|</span>Products<span>|</span>Contact Us</div>
<div class="abs social" style="left:885px"></div>
<div class="abs social" style="left:915px"></div>
<div class="abs social" style="left:946px"></div>
</body>
</html>
```